Seeking funky, innovative business cards

I am looking to refresh our current business cards to something more engaging, visual and impactful. We are a management consultancy firm, see website (www.larkstone-partners.com.au). I've included our colour scheme, sample of the slides we use and our old business cards. We would like our cards to have icons. The card should display:- Name- Title- Mobile number- Address- Email address- Website - Company logo- Our purpose statement "we build workplaces people are proud to join"

Contact Information for Business Card

Brennan Ulfsson
Consultant
0468 927 341
Level 3, 218 Wexley Street, Melbourne 3000
brennan@larkstone-partners.com.au
www.larkstone-partners.com.au

Purpose statement "we build workplaces people are proud to join"
LOGO available in google images

Font styles to use
Other font styles liked:
• Open Sans Light, Bebas Neue (open to other cool foints)

Colors
ffc214
5c5c5c
f5f5f5
fefefe

Requirements
Must have
• - Name
• - Title
• - Mobile number
• - Address
• - Email address
• - Website
• - Company logo
• - Our purpose statement "we build workplaces people are proud to join"
Nice to have
• - Icons
• - Colour (see our colour scheme"

```html
<!DOCTYPE html>
<html lang="en">
<head>
<meta charset="utf-8">
<title>Larkstone Partners – Business Card</title>
<link href="https://fonts.googleapis.com/css2?family=Roboto:ital,wght@0,300;0,400;0,500;1,500&display=swap" rel="stylesheet">
<style>
  :root {
    --brand-yellow: #ffc220;
    --ink-white: #fefefe;
    --backdrop: #c2c2c2;
  }
  html, body {
    margin: 0;
    padding: 0;
    width: 1200px;
    height: 1200px;
    overflow: hidden;
    background: var(--backdrop);
    font-family: "Roboto", Arial, sans-serif;
    color: var(--ink-white);
  }
  .canvas {
    position: relative;
    width: 1200px;
    height: 1200px;
  }
  .card {
    position: absolute;
    left: 218px;
    width: 799px;
    height: 457px;
    background: var(--brand-yellow);
  }
  .card--front { top: 115px; }
  .card--back  { top: 638px; }

  /* Front */
  .identity {
    position: absolute;
    right: 462px;
    top: 196px;
    text-align: right;
  }
  .identity__name {
    font-size: 30px;
    font-weight: 500;
    line-height: 36px;
    letter-spacing: 0.2px;
  }
  .identity__title {
    font-size: 20px;
    font-weight: 500;
    line-height: 24px;
  }
  .divider {
    position: absolute;
    left: 369px;
    top: 153px;
    width: 2px;
    height: 146px;
    background: var(--ink-white);
  }
  .contact {
    position: absolute;
    left: 400px;
    top: 157px;
    font-size: 19px;
    font-weight: 400;
  }
  .contact__address {
    line-height: 24px;
    margin-bottom: 13px;
  }
  .contact__row {
    display: flex;
    align-items: center;
    height: 25.5px;
  }
  .contact__icon {
    width: 20px;
    height: 20px;
    margin-right: 11px;
    flex: none;
  }

  /* Back */
  .wordmark {
    position: absolute;
    left: 0;
    right: 0;
    top: 218px;
    display: flex;
    justify-content: center;
    align-items: center;
    gap: 14px;
  }
  .wordmark__dot {
    width: 18px;
    height: 18px;
    border-radius: 50%;
    background: var(--ink-white);
  }
  .wordmark__name {
    font-size: 58px;
    font-weight: 300;
    line-height: 1;
  }
  .purpose {
    position: absolute;
    left: 0;
    right: 0;
    top: 381px;
    text-align: center;
    font-size: 21px;
    font-weight: 500;
    font-style: italic;
  }
</style>
</head>
<body>
<main class="canvas">
  <section class="card card--front" aria-label="Card front">
    <div class="identity">
      <div class="identity__name">Brennan Ulfsson</div>
      <div class="identity__title">Consultant</div>
    </div>
    <div class="divider"></div>
    <div class="contact">
      <div class="contact__address">Level 3, 218 Wexley Street,<br>Melbourne 3000</div>
      <div class="contact__row">
        <svg class="contact__icon" viewBox="0 0 24 24" aria-hidden="true"><path fill="#fefefe" d="M6.6 10.8a15.1 15.1 0 0 0 6.6 6.6l2.2-2.2a1 1 0 0 1 1-.25 11.4 11.4 0 0 0 3.6.57 1 1 0 0 1 1 1V20a1 1 0 0 1-1 1A17 17 0 0 1 3 4a1 1 0 0 1 1-1h3.5a1 1 0 0 1 1 1c0 1.25.2 2.450.57 3.57a1 1 0 0 1-.25 1z"/></svg>
        <span>0468 927 341</span>
      </div>
      <div class="contact__row">
        <svg class="contact__icon" viewBox="0 0 24 24" aria-hidden="true"><path fill="#fefefe" d="M3 6h18v12H3z"/><path fill="none" stroke="#ffc220" stroke-width="1.6" d="M3.5 6.5 12 13l8.5-6.5"/></svg>
        <span>brennan@larkstone-partners.com.au</span>
      </div>
      <div class="contact__row">
        <svg class="contact__icon" viewBox="0 0 24 24" aria-hidden="true"><circle cx="12" cy="12" r="9" fill="#fefefe"/><path fill="#ffc220" d="M7 7.5c2 .3 2.6 1.7 2 3-.5 1 .8 2 1.8 2.2.9.2.6 2 .2 3.3-1.5-.3-3.8-1.8-4.5-4-.4-1.4-.3-3 .5-4.5zM13.5 5.5c1.5.2 2.5 1.2 2 2.3-.4.9-1.8.6-2.5 1.5-.5.7-1.8.3-1.6-.8.2-1.2 1-2.5 2.1-3z"/></svg>
        <span>www.larkstone-partners.com.au</span>
      </div>
    </div>
  </section>

  <section class="card card--back" aria-label="Card back">
    <div class="wordmark">
      <span class="wordmark__dot"></span>
      <span class="wordmark__name">Larkstone Partners</span>
    </div>
    <div class="purpose">we build workplaces people are proud to join</div>
  </section>
</main>
</body>
</html>
```